Dentistry

Dentist's personal business card. No logo needed. The card shoul deliver the massage of reliability, professionalism, experience.
Please ad the full brief of the project: down the line it says: the winning look should be precise and pristine NO pictures of Teeth, smiles, instruments etc.

The details to be desplaid are:
Dr. Rob Tavolen
Doctor of Dental Surgery
PHD
Web. Www.drtavolen.com
Email. Rob@drtavolen.com
Tel 07742318590
Surgery address. 27Bferndale road London SW4 8QT UK
62 Wexley Row London SW3 2HN. Uk

Reason: Decided to make the payment unrefundable in order to get more designers involved.

Requirements
Should not have
• Logo, teeth, smile any sort of instruments.

```html
<!DOCTYPE html>
<html lang="en">
<head>
<meta charset="utf-8">
<title>Dr. Rob Tavolen – Business Card</title>
<link rel="stylesheet" href="https://fonts.googleapis.com/css2?family=Exo+2:wght@400;700&display=swap">
<style>
  :root {
    --card-navy: #16113a;
    --accent-blue: #0080c8;
    --name-white: #ffffff;
    --page-bg: #ffffff;
  }
  html, body {
    margin: 0;
    padding: 0;
    width: 1200px;
    height: 777px;
    overflow: hidden;
    background: var(--page-bg);
  }
  .business-card {
    display: block;
    width: 1200px;
    height: 777px;
    font-family: "Exo 2", sans-serif;
  }
  .card-face { fill: var(--card-navy); }
  .title-band { fill: var(--accent-blue); }
  .doctor-name {
    fill: var(--name-white);
    font-weight: 700;
    font-size: 61px;
  }
  .degree {
    fill: var(--accent-blue);
    font-weight: 400;
    font-size: 36px;
  }
  .profession {
    fill: var(--card-navy);
    font-weight: 400;
    font-size: 37px;
    letter-spacing: 1px;
  }
</style>
</head>
<body>
<svg class="business-card" viewBox="0 0 1200 777" xmlns="http://www.w3.org/2000/svg">
  <defs>
    <clipPath id="card-shape">
      <rect x="0" y="0" width="1200" height="777" rx="45" ry="45"/>
    </clipPath>
  </defs>
  <g clip-path="url(#card-shape)">
    <rect class="card-face" x="0" y="0" width="1200" height="777"/>
    <rect class="title-band" x="0" y="530" width="1200" height="68"/>
  </g>
  <text class="doctor-name" x="813" y="380" text-anchor="end">Dr. Rob Tavolen</text>
  <text class="degree" x="813" y="442" text-anchor="end">PHD</text>
  <text class="profession" x="598" y="575" text-anchor="middle">DOCTOR OF DENTAL SURGERY</text>
</svg>
</body>
</html>
```